Brightfen Business Card Redesign & Logo Update

We need to update our business cards to something more modern and fresh. Brightfen can provide the current color schemes and old design examples, but welcome creativity in helping us with this redesign. PLEASE NOTE that we no longer utilize the "tree" and/or "leaf" imagery in our branding. If able would apprecaite an update on the quality of our "words only" logo in Ai. / PNG formats too.

Target Market(s)

Investors, landowners, corporate partners, contractors

Industry/Entity Type

Environmental Restoration & Conservation

Contact Information for Business Card

Logo, persons name, title, mailing address, phone and email, website url

Font styles to use
Other font styles liked:
• Merriweather

Requirements
Nice to have
• Logo, persons name, title, mailing address, phone and email, website url, but open to ideams
Should not have
• No all back backgrounds

```html
<!DOCTYPE html>
<html lang="en">
<head>
<meta charset="utf-8">
<title>Brightfen Business Card</title>
<link rel="stylesheet" href="https://fonts.googleapis.com/css2?family=Open+Sans:wght@400;600;700;800&family=Oswald:wght@600&display=swap">
<style>
  :root {
    --backdrop: #d9d9d7;
    --card: #ffffff;
    --green: #17803d;
    --orange: #ef7d22;
    --ink: #1a1a1a;
    --grey: #6b6b6b;
    --rule: #9cc7a8;
  }
  * { box-sizing: border-box; margin: 0; padding: 0; }
  html, body {
    width: 1200px; height: 801px; overflow: hidden;
    background: var(--backdrop);
    font-family: "Open Sans", Arial, sans-serif;
  }
  .stage {
    position: relative; width: 1200px; height: 801px;
    display: flex; align-items: center; justify-content: center; gap: 60px;
  }
  .card {
    position: relative; width: 520px; height: 297px;
    background: var(--card);
    border-bottom: 4px solid var(--green);
    box-shadow: 0 10px 24px rgba(0,0,0,0.18);
  }
  /* contact side */
  .identity {
    position: absolute; left: 40px; top: 78px; width: 200px; text-align: right;
  }
  .person-name {
    color: var(--green); font-weight: 700; font-size: 20px; letter-spacing: 0.5px;
    text-transform: uppercase; white-space: nowrap;
  }
  .person-title { color: var(--grey); font-size: 15px; margin-top: 2px; }
  .divider {
    position: absolute; left: 262px; top: 62px; width: 1px; height: 88px;
    background: var(--rule);
  }
  .contact-list {
    position: absolute; left: 282px; top: 58px; list-style: none;
  }
  .contact-list li {
    display: flex; align-items: center; gap: 8px;
    color: var(--grey); font-size: 14px; line-height: 26px;
  }
  .contact-list svg { width: 13px; height: 13px; flex: none; }
  .address {
    position: absolute; left: 40px; right: 40px; bottom: 46px;
    color: var(--grey); font-size: 15px; text-align: center;
  }
  /* logo side */
  .brand {
    position: absolute; inset: 0;
    display: flex; flex-direction: column; align-items: center; justify-content: center;
  }
  .brand-name {
    font-family: "Oswald", "Arial Narrow", sans-serif; font-weight: 600;
    font-size: 86px; line-height: 1; color: var(--green);
    text-transform: uppercase; letter-spacing: 2px;
  }
  .brand-tagline {
    font-family: "Oswald", "Arial Narrow", sans-serif; font-weight: 600;
    font-size: 22px; color: var(--ink); text-transform: uppercase;
    letter-spacing: 1px; margin-top: 8px;
  }
</style>
</head>
<body>
<main class="stage">
  <section class="card card--contact">
    <div class="identity">
      <p class="person-name">Darin Halvorsen</p>
      <p class="person-title">President</p>
    </div>
    <div class="divider"></div>
    <ul class="contact-list">
      <li>
        <svg viewBox="0 0 16 16" aria-hidden="true"><circle cx="8" cy="8" r="8" fill="var(--orange)"/><path d="M5.2 4.2l1.6-.4.8 2-1 .8a5 5 0 0 0 2.8 2.8l.8-1 2 .8-.4 1.6c-3.6.2-6.8-3-6.6-6.6z" fill="#fff"/></svg>
        555-014-2290
      </li>
      <li>
        <svg viewBox="0 0 16 16" aria-hidden="true"><rect x="1" y="3" width="14" height="10" rx="1" fill="var(--orange)"/><path d="M1.5 3.8L8 8.8l6.5-5" fill="none" stroke="#fff" stroke-width="1.4"/></svg>
        dhalvorsen@brightfen.com
      </li>
      <li>
        <svg viewBox="0 0 16 16" aria-hidden="true"><circle cx="8" cy="8" r="8" fill="var(--orange)"/><circle cx="8" cy="8" r="5" fill="none" stroke="#fff" stroke-width="1.2"/><path d="M3 8h10M8 3c-2.4 2.8-2.4 7.2 0 10M8 3c2.4 2.8 2.4 7.2 0 10" fill="none" stroke="#fff" stroke-width="1"/></svg>
        www.brightfen.com
      </li>
    </ul>
    <p class="address">18 Harbor Crest Lane, Seaview CA 90412</p>
  </section>

  <section class="card card--brand">
    <div class="brand">
      <p class="brand-name">Brightfen</p>
      <p class="brand-tagline">Environmental Credit Company</p>
    </div>
  </section>
</main>
</body>
</html>
```